Business card design for Velmora Engineering Tandem

We need a new business card design along with all the necessary to place an order. The company is Velmora Engineering Tandem and we recently updated our logo.

```html
<!DOCTYPE html>
<html lang="en">
<head>
<meta charset="utf-8">
<title>Velmora Engineering Tandem — Business Card</title>
<link href="https://fonts.googleapis.com/css2?family=Montserrat:wght@400;500;700&display=swap" rel="stylesheet">
<style>
  :root {
    --stage: #2b2b2b;
    --card-front: #969696;
    --card-back: #ffffff;
    --brand-gold: #e2b928;
    --brand-grey: #8f8f8f;
    --ink: #2a2a2a;
    --white: #ffffff;
  }
  * { box-sizing: border-box; margin: 0; padding: 0; }
  html, body {
    width: 1200px; height: 875px; overflow: hidden;
    background: var(--stage);
    font-family: "Montserrat", Arial, sans-serif;
  }
  .stage {
    width: 1200px; height: 875px;
    display: flex; flex-direction: column; align-items: center; justify-content: center;
    gap: 48px;
  }
  .card {
    width: 560px; height: 320px;
    border-radius: 18px;
    position: relative;
  }
  .card-front {
    background: var(--card-front);
    display: flex; align-items: center; justify-content: center;
    padding: 0 40px;
  }
  .wordmark {
    display: flex; align-items: center; gap: 14px;
    font-weight: 700; letter-spacing: 0.03em; text-transform: uppercase;
  }
  .wordmark-square { width: 16px; height: 16px; background: var(--brand-gold); flex: none; }
  .card-front .wordmark { color: var(--white); font-size: 24px; white-space: nowrap; }
  .card-back {
    background: var(--card-back);
    display: flex; align-items: center;
    padding: 0 36px 0 40px;
  }
  .card-back .wordmark { color: var(--brand-grey); font-size: 16px; width: 190px; line-height: 1.25; gap: 10px; }
  .card-back .wordmark-square { width: 12px; height: 12px; }
  .divider { width: 2px; height: 150px; background: var(--brand-gold); margin: 0 26px 0 18px; flex: none; }
  .contact { color: var(--ink); font-size: 12.5px; line-height: 1.45; }
  .contact-name { color: var(--brand-gold); font-size: 21px; font-weight: 700; line-height: 1.2; }
  .contact-role { margin-bottom: 10px; }
  .contact-address { margin-bottom: 10px; }
  .contact-line { display: flex; align-items: center; gap: 8px; white-space: nowrap; }
  .contact-line svg { width: 12px; height: 12px; flex: none; fill: var(--brand-gold); }
</style>
</head>
<body>
<main class="stage">
  <section class="card card-front" aria-label="Card front">
    <div class="wordmark"><span class="wordmark-square"></span>Velmora Engineering Tandem</div>
  </section>

  <section class="card card-back" aria-label="Card back">
    <div class="wordmark"><span class="wordmark-square"></span>Velmora Engineering Tandem</div>
    <div class="divider"></div>
    <div class="contact">
      <p class="contact-name">Marcus Delaney</p>
      <p class="contact-role">Managing Director</p>
      <p class="contact-address">42 Harbor Point Drive<br>Easton, PA 18042 USA</p>
      <p class="contact-line">
        <svg viewBox="0 0 24 24"><path d="M6.6 10.8a15.2 15.2 0 0 0 6.6 6.6l2.2-2.2c.3-.3.7-.4 1-.2 1.1.4 2.3.6 3.6.6.6 0 1 .4 1 1V20c0 .6-.4 1-1 1C10.6 21 3 13.4 3 4c0-.6.4-1 1-1h3.5c.6 0 1 .4 1 1 0 1.3.2 2.5.6 3.6.1.3 0 .7-.2 1z"/></svg>
        (555)214-7780
      </p>
      <p class="contact-line">
        <svg viewBox="0 0 24 24"><path d="M2 5h20v14H2z M3 6l9 7 9-7" /></svg>
        info@velmoratandem.com
      </p>
      <p class="contact-line">
        <svg viewBox="0 0 24 24"><path d="M12 2a10 10 0 1 0 0 20 10 10 0 0 0 0-20zm6.9 6h-3a15 15 0 0 0-1.3-3.9A8 8 0 0 1 18.9 8zM12 4c.9 1.2 1.6 2.6 2 4h-4c.4-1.4 1.1-2.8 2-4zM4.3 14a8 8 0 0 1 0-4h3.4a16 16 0 0 0 0 4zm.8 2h3a15 15 0 0 0 1.3 3.9A8 8 0 0 1 5.1 16zm3-8h-3a8 8 0 0 1 4.3-3.9C8.8 5.3 8.4 6.6 8.1 8zM12 20c-.9-1.2-1.6-2.6-2-4h4c-.4 1.4-1.1 2.8-2 4zm2.3-6H9.7a14 14 0 0 1 0-4h4.6a14 14 0 0 1 0 4zm.3 5.9c.6-1.200 1-2.5 1.3-3.9h3a8 8 0 0 1-4.3 3.9zm1.7-5.9a16 16 0 0 0 0-4h3.4a8 8 0 0 1 0 4z"/></svg>
        www.velmoratandem.com
      </p>
    </div>
  </section>
</main>
</body>
</html>
```